real esate business card with company logo and name

we need a business card design for a real esate company

The company name is Walsh & Brand Pty Ltd, and we have our logo designed and will upload. We want classic or moden feel. Black or white background. looks more textured. Should include folowinginformations
Owen Walsh and Lucy Brand
Sales Agents & Onsite Manager
p: 07 5948 2063
F: 07 5948 2174
M:0431 857 219
3/42 Marlow Crescent, FERNLEA QLD 4213

We want this business card looks professonal. Thank you in advance.

Industry/Entity Type

Real Estate Agent

Contact Information for Business Card

Owen Walsh and Lucy Brand
Onsite Manager & Sales Agents
p: 07 5948 2063
M:0431 857 219

Font styles to use
Serif

Colors
000000
fbfbfb
333333
959595

Requirements
Must have
• company logo and name, black or white back ground

```html
<!DOCTYPE html>
<html lang="en">
<head>
<meta charset="utf-8">
<title>Walsh &amp; Brand Pty Ltd – Business Card</title>
<link rel="stylesheet" href="https://fonts.googleapis.com/css2?family=Cinzel:wght@400;600&display=swap">
<style>
  :root {
    --black: #000000;
    --ink: #0d0d0d;
    --white: #fbfbfb;
    --charcoal: #333333;
    --silver: #959595;
    --silver-light: #c4c4c4;
    --backdrop: #e6e4e1;
    --serif: "Cinzel", "Times New Roman", serif;
  }
  * { box-sizing: border-box; margin: 0; padding: 0; }
  html, body { width: 1200px; height: 913px; overflow: hidden; }
  body {
    background: var(--backdrop);
    display: flex;
    align-items: center;
    justify-content: center;
    gap: 60px;
    font-family: var(--serif);
  }
  .card {
    position: relative;
    width: 525px;
    height: 300px;
    border-radius: 16px;
    overflow: hidden;
    box-shadow: 0 10px 28px rgba(0,0,0,.28);
  }

  /* Front: black face with contact details */
  .card--front {
    background: radial-gradient(ellipse at 40% 30%, #2a2a2a 0%, var(--ink) 55%, var(--black) 100%);
    color: var(--white);
  }
  .card--front .edge-band {
    position: absolute; left: 0; top: 0; bottom: 0; width: 30px;
    background: linear-gradient(to bottom, var(--white) 0 58%, var(--silver) 58% 100%);
  }
  .card--front .edge-band::after {
    content: ""; position: absolute; right: -8px; top: 58%; bottom: 0; width: 8px;
    background: var(--silver-light);
  }
  .contact {
    position: absolute; left: 56px; top: 36px; width: 270px;
  }
  .contact__names {
    font-size: 19px; font-weight: 400; letter-spacing: .02em; line-height: 1.2;
  }
  .contact__role {
    margin-top: 4px; font-size: 10.5px; color: var(--silver); letter-spacing: .04em;
  }
  .contact__address {
    margin-top: 12px; font-size: 11.5px; line-height: 1.45; color: var(--white);
  }
  .contact__phones {
    list-style: none; position: absolute; left: 56px; bottom: 40px;
    font-size: 11.5px; line-height: 1.75; color: var(--white);
  }
  .contact__phones li { display: flex; align-items: center; gap: 9px; }
  .contact__phones svg { width: 11px; height: 11px; fill: var(--silver-light); }

  .brand {
    display: flex; align-items: center; gap: 10px;
    font-family: var(--serif); font-weight: 600; letter-spacing: .06em;
  }
  .brand__mark { width: 14px; height: 14px; }
  .card--front .brand {
    position: absolute; right: 34px; top: 132px;
    font-size: 15px; color: var(--silver-light);
  }
  .card--front .brand__mark { background: var(--silver-light); }

  /* Back: white face with company name */
  .card--back { background: var(--white); }
  .card--back .edge-band {
    position: absolute; right: 0; top: 0; bottom: 0; width: 42px;
    background: linear-gradient(to bottom, var(--black) 0 30%, var(--silver) 30% 100%);
  }
  .card--back .edge-band::before {
    content: ""; position: absolute; left: -8px; top: 30%; bottom: 0; width: 8px;
    background: var(--silver-light);
  }
  .card--back .brand {
    position: absolute; left: 0; right: 42px; top: 0; bottom: 0;
    justify-content: center;
    font-size: 20px; color: var(--charcoal);
  }
  .card--back .brand__mark { background: var(--charcoal); }
</style>
</head>
<body>

  <section class="card card--front" aria-label="Business card front">
    <div class="edge-band"></div>

    <div class="contact">
      <h1 class="contact__names">Owen Walsh &amp; Lucy Brand</h1>
      <p class="contact__role">Sales Agents &amp; Onsite Manager</p>
      <p class="contact__address">3/42 Marlow Crescent,<br>FERNLEA QLD 4213</p>
    </div>

    <ul class="contact__phones">
      <li>
        <svg viewBox="0 0 24 24" aria-hidden="true"><path d="M6.6 10.8a15 15 0 0 0 6.6 6.6l2.2-2.2a1 1 0 0 1 1-.25 11.4 11.4 0 0 0 3.6.6 1 1 0 0 1 1 1V20a1 1 0 0 1-1 1A17 17 0 0 1 3 4a1 1 0 0 1 1-1h3.5a1 1 0 0 1 1 1c0 1.25.2 2.45.6 3.6a1 1 0 0 1-.25 1z"/></svg>
        07 5948 2063
      </li>
      <li>
        <svg viewBox="0 0 24 24" aria-hidden="true"><path d="M6 2h10v6H6z M3 9h18v10H3z M6 20h12v2H6z"/></svg>
        07 5948 2174
      </li>
      <li>
        <svg viewBox="0 0 24 24" aria-hidden="true"><path d="M7 1h10a2 2 0 0 1 2 2v18a2 2 0 0 1-2 2H7a2 2 0 0 1-2-2V3a2 2 0 0 1 2-2zm0 3v14h10V4z"/></svg>
        0431 857 219
      </li>
    </ul>

    <div class="brand">
      <span class="brand__mark" aria-hidden="true"></span>
      <span class="brand__name">WALSH &amp; BRAND PTY LTD.</span>
    </div>
  </section>

  <section class="card card--back" aria-label="Business card back">
    <div class="edge-band"></div>
    <div class="brand">
      <span class="brand__mark" aria-hidden="true"></span>
      <span class="brand__name">WALSH &amp; BRAND PTY LTD.</span>
    </div>
  </section>

</body>
</html>
```